Alaska Law Firm Needs a Sticker Design

We need a design for stickers to put on already-printed brochures. We mail the brochures to potential clients so they can learn more about accident-induced injuries, insurance claims, legal representation, and our own law firm.

One of our lawyers wrote a book that provides a helpful overview of personal injury claims. We are offering this book for free to anyone who calls and requests it. Therefore, the sticker design should include one of the following phrases, or something very similar:
a) "Still have questions? Call and request our book-- for free!"
b) "Still have questions about auto accident claims? Call and request our book today."
c) "Still have questions about filing a claim? Call and request a free copy of our book."
d) "Still have questions? Call us today to request a free copy of our book, Clear Lanes Ahead."
e) "To learn more about automobile accidents and insurance, call today and request a free copy of our book."

The sticker should be approximately 3"x3" and may be a circle, square, rectangle, or ellipsis. The sticker will be placed on the back of the folder, which is light blue. We would like the sticker to match the color scheme of our website and the folder.

I will upload an image of the book cover as soon as I obtain it.

Law Firm

Font styles to use
Serif
Sans Serif

Requirements
Should not have
• Bright colors that aren't already used in the folder design. e.g. no bright orange, pink, chartreuse, turquoise, yellow, red.

```html
<!DOCTYPE html>
<html lang="en">
<head>
<meta charset="utf-8">
<title>Free Book Sticker</title>
<link href="https://fonts.googleapis.com/css2?family=Ubuntu:wght@400;500;700&display=swap" rel="stylesheet">
<style>
  :root {
    --backdrop-light: #f4f4f4;
    --backdrop-dark: #d9d9d9;
    --ring-grey: #5e5e5e;
    --ring-navy: #0b3763;
    --ring-white: #ffffff;
    --face-core: #f3f8fd;
    --face-mid: #dbe9f7;
    --face-edge: #a9c8e8;
    --ink-navy: #0d3a68;
    --ink-deep: #061f3a;
    --ink-grey: #5a6470;
    --ink-white: #ffffff;
  }
  html, body {
    margin: 0;
    padding: 0;
    overflow: hidden;
  }
  .canvas {
    width: 1200px;
    height: 1200px;
    position: relative;
    overflow: hidden;
    background: radial-gradient(circle at 50% 45%, var(--backdrop-light) 0%, var(--backdrop-dark) 100%);
    font-family: "Ubuntu", sans-serif;
  }
  .sticker {
    position: absolute;
    inset: 0;
    width: 1200px;
    height: 1200px;
  }
  .ring-grey { fill: var(--ring-grey); }
  .ring-navy { fill: var(--ring-navy); }
  .ring-white { fill: var(--ring-white); }
  .sticker-face { fill: url(#faceGradient); }
  .message { font-family: "Ubuntu", sans-serif; }
  .w-navy { fill: var(--ink-navy); }
  .w-deep { fill: var(--ink-deep); }
  .w-grey { fill: var(--ink-grey); }
  .w-bold { font-weight: 700; }
  .w-medium { font-weight: 500; }
  .w-regular { font-weight: 400; }
  .caller-figure {
    position: absolute;
    left: 250px;
    top: 566px;
    width: 148px;
    height: 172px;
    background: var(--ink-navy);
    border-radius: 56px 56px 14px 14px;
  }
  .call-label {
    position: absolute;
    left: 250px;
    top: 670px;
    width: 148px;
    text-align: center;
    font-family: "Ubuntu", sans-serif;
    font-weight: 400;
    font-size: 56px;
    line-height: 1;
    color: var(--ink-white);
  }
</style>
</head>
<body>
<div class="canvas">
  <svg class="sticker" viewBox="0 0 1200 1200" xmlns="http://www.w3.org/2000/svg">
    <defs>
      <radialGradient id="faceGradient" cx="50%" cy="48%" r="55%">
        <stop offset="0%" stop-color="var(--face-core)"/>
        <stop offset="65%" stop-color="var(--face-mid)"/>
        <stop offset="100%" stop-color="var(--face-edge)"/>
      </radialGradient>
    </defs>
    <circle class="ring-grey" cx="599" cy="563" r="430"/>
    <circle class="ring-navy" cx="652" cy="616" r="430"/>
    <circle class="ring-white" cx="569" cy="648" r="430"/>
    <circle class="sticker-face" cx="610" cy="610" r="430"/>

    <g class="message">
      <text x="370" y="379" textLength="491" lengthAdjust="spacingAndGlyphs">
        <tspan class="w-navy w-regular" font-size="70">"To learn </tspan><tspan class="w-navy w-bold" font-size="100">more</tspan>
      </text>
      <text x="315" y="460" textLength="559" lengthAdjust="spacingAndGlyphs">
        <tspan class="w-navy w-bold" font-size="95">about </tspan><tspan class="w-grey w-regular" font-size="62">automobile</tspan>
      </text>
      <text x="303" y="546" textLength="580" lengthAdjust="spacingAndGlyphs">
        <tspan class="w-deep w-medium" font-size="112">accidents </tspan><tspan class="w-navy w-regular" font-size="66">and</tspan>
      </text>
      <text class="w-navy w-medium" x="414" y="635" font-size="108" textLength="510" lengthAdjust="spacingAndGlyphs">insurance,</text>
      <text x="423" y="705" textLength="508" lengthAdjust="spacingAndGlyphs">
        <tspan class="w-deep w-regular" font-size="66">today </tspan><tspan class="w-grey w-regular" font-size="62">and request</tspan>
      </text>
      <text class="w-grey w-medium" x="436" y="785" font-size="76" textLength="394" lengthAdjust="spacingAndGlyphs">a free copy</text>
      <text class="w-navy w-bold" x="315" y="877" font-size="98" textLength="610" lengthAdjust="spacingAndGlyphs">of our book."</text>
    </g>
  </svg>

  <div class="caller-figure" role="img" aria-label="Icon of a person on a phone call"></div>
  <div class="call-label">call</div>
</div>
</body>
</html>
```